Brand new letterhead, business card, email signature etc.

We are a financial company in London, UK. Our website is www.marlowvane.com. We're wanting a complete remodel of the company colours, letter head, business cards, email signatures, etc. Looking to keep the same font for the company name. I have upload a colour palette that we want to work with. We're looking for company letterhead for outgoing letters/ correspondence, letterhead for internal documentation, email signatures, e-letters. etc. Ultimately we will redesign the entire website also. It is important that our clients get a strong, secure, warm, trustworthy, solid feeling and first impression.
Updates

Designs look the same

Target Market(s)

Institutional investors, (ultra) high net worth individuals

Industry/Entity Type

Finance, Invesments banking.

Font styles to use
Other font styles liked:
• Current font is "Champagne & Limousines"

Requirements
Must have
• Must use the colours provided on the PDF uploaded to the portal. The purple = main colour. The red = accent colour.
Nice to have
• Nice to use same font as now for the company name "Corvane". Font is "Champagne & Limousines". Nice to have some reference to the old logo flower, but only subtle.
Should not have
• Do not use the colour red from our website. Use the colours provided on the colour palette PDF that I uploaded in the portal.

```html
<!DOCTYPE html>
<html lang="en">
<head>
<meta charset="utf-8">
<title>Corvane business cards</title>
<link href="https://fonts.googleapis.com/css2?family=Josefin+Sans:wght@300;400&display=swap" rel="stylesheet">
<style>
  :root {
    --backdrop: #7f97b8;
    --paper: #ffffff;
    --accent-red: #e2452f;
    --accent-red-light: #ea5e48;
    --main-purple: #3b2230;
    --ink: #3a3336;
  }
  * { box-sizing: border-box; margin: 0; padding: 0; }
  html, body {
    width: 1200px; height: 876px; overflow: hidden;
    background: var(--backdrop);
    font-family: "Josefin Sans", sans-serif;
  }
  .canvas {
    width: 1200px; height: 876px;
    display: flex; align-items: center; justify-content: center; gap: 40px;
  }
  .card {
    position: relative;
    width: 540px; height: 309px;
    background: var(--paper);
    overflow: hidden;
    box-shadow: 0 10px 24px rgba(30, 40, 70, 0.25);
  }
  .card-bands { position: absolute; inset: 0; width: 100%; height: 100%; }
  .brand {
    position: absolute; display: flex; align-items: center; gap: 14px;
  }
  .brand-square {
    flex: none; width: 46px; height: 46px; border: 1px solid var(--ink);
  }
  .brand-name {
    font-weight: 300; color: var(--ink); white-space: nowrap;
    letter-spacing: 0.32em; text-transform: uppercase;
  }
  .card--front .brand { left: 120px; top: 120px; }
  .card--front .brand-name { font-size: 40px; }
  .card--back .brand { left: 40px; top: 72px; }
  .card--back .brand-square { width: 36px; height: 36px; }
  .card--back .brand-name { font-size: 28px; }
  .website {
    position: absolute; left: 22px; bottom: 22px;
    color: var(--paper); font-size: 11px; letter-spacing: 0.03em;
  }
  .contact-block {
    position: absolute; right: 34px; top: 124px; text-align: right;
  }
  .person-name {
    color: var(--accent-red); font-size: 22px; font-weight: 400;
    text-transform: uppercase; letter-spacing: 0.01em; white-space: nowrap;
  }
  .person-role { color: var(--ink); font-size: 15px; margin-top: 2px; }
  .contact-list { list-style: none; margin-top: 12px; }
  .contact-list li {
    display: flex; justify-content: flex-end; align-items: center; gap: 10px;
    color: var(--ink); font-size: 11px; line-height: 1.3; margin-bottom: 6px;
  }
  .contact-icon { width: 13px; height: 13px; flex: none; fill: var(--accent-red); }
</style>
</head>
<body>
<main class="canvas">

  <section class="card card--back" aria-label="Business card, contact side">
    <svg class="card-bands" viewBox="0 0 540 309" aria-hidden="true">
      <polygon points="0,0 300,0 328,26 400,26 420,44 0,44" fill="var(--accent-red)"/>
      <polygon points="0,226 180,226 205,252 0,252" fill="var(--accent-red-light)"/>
      <polygon points="0,240 160,240 170,252 0,252" fill="var(--accent-red)"/>
      <polygon points="0,252 205,252 230,278 540,278 540,309 0,309" fill="var(--main-purple)"/>
      <polygon points="222,236 262,236 278,252 238,252" fill="var(--accent-red)"/>
    </svg>
    <div class="brand">
      <span class="brand-square"></span>
      <span class="brand-name">Corvane</span>
    </div>
    <div class="contact-block">
      <h2 class="person-name">Elliot Harrow</h2>
      <p class="person-role">Director</p>
      <ul class="contact-list">
        <li>020 7946 0381
          <svg class="contact-icon" viewBox="0 0 16 16"><path d="M4 1l3 3-2 2c1 2 3 4 5 5l2-2 3 3-2 3C7 15 1 9 1 3z"/></svg></li>
        <li>e.harrow@marlowvane.com
          <svg class="contact-icon" viewBox="0 0 16 16"><path d="M1 3h14v10H1z M1 3l7 6 7-6" stroke="#fff" stroke-width="1"/></svg></li>
        <li>Head Office:<br>14 Carrow Lane, suite 3
          <svg class="contact-icon" viewBox="0 0 16 16"><path d="M8 1a5 5 0 0 1 5 5c0 4-5 9-5 9S3 10 3 6a5 5 0 0 1 5-5z"/><circle cx="8" cy="6" r="2" fill="#fff"/></svg></li>
      </ul>
    </div>
  </section>

  <section class="card card--front" aria-label="Business card, brand side">
    <svg class="card-bands" viewBox="0 0 540 309" aria-hidden="true">
      <polygon points="0,10 300,10 320,34 470,34 490,52 0,52" fill="var(--accent-red)"/>
      <polygon points="300,10 380,10 400,34 320,34" fill="var(--accent-red-light)"/>
      <polygon points="455,62 540,62 540,150 520,90 470,78" fill="var(--main-purple)"/>
      <polygon points="0,246 260,246 285,270 0,270" fill="var(--accent-red)"/>
      <polygon points="0,270 285,270 285,309 0,309" fill="var(--accent-red)"/>
      <polygon points="260,258 300,258 326,284 540,284 540,309 285,309 285,270" fill="var(--main-purple)"/>
      <polygon points="310,250 350,250 366,266 326,266" fill="var(--accent-red)"/>
    </svg>
    <div class="brand">
      <span class="brand-square"></span>
      <span class="brand-name">Corvane</span>
    </div>
    <p class="website">www.marlowvane.com</p>
  </section>

</main>
</body>
</html>
```